Business Card Design for company

We want new business cards. We'd like something different-- yet still highly professional. Our tagline is Providing leadership, delivering success. Stock photos are ok, as long as they are relevant and look upscale.

Target Market(s)

Architecture/Business Management Consulting/Engineering Consulting

Contact Information for Business Card

dark gray background with pops of blue might be good, but you tell me. You're the designers. Rounded corners might be nice, but again, you tell me.

Font styles to use
Serif
Sans Serif

Colors
3276b5
5c5c5c
9d9d9d
fbfbfb

Requirements
Nice to have
• Something different, but still very professional.

```html
<!DOCTYPE html>
<html lang="en">
<head>
<meta charset="utf-8">
<title>Talven Group — Business Card</title>
<link rel="stylesheet" href="https://fonts.googleapis.com/css2?family=Montserrat:wght@500;600;700&family=Open+Sans:wght@400;600&display=swap">
<style>
  :root {
    --stage: #2a2a2b;
    --card-light: #ededed;
    --card-dark: #4a4c50;
    --brand-blue: #27609a;
    --ink-gray: #4a4c50;
    --text-gray: #3a3b3d;
    --rule: #9d9d9d;
    --white: #fbfbfb;
  }
  * { margin: 0; padding: 0; box-sizing: border-box; }
  html, body { width: 1200px; height: 1200px; overflow: hidden; }
  body {
    background: var(--stage);
    position: relative;
    font-family: "Open Sans", Arial, sans-serif;
  }
  .card {
    position: absolute;
    top: 310px;
    width: 364px;
    height: 594px;
    box-shadow: 0 3px 8px rgba(0,0,0,.5);
  }
  .card--front { left: 234px; background: var(--card-light); }
  .card--back  { left: 630px; width: 366px; background: var(--card-dark); }

  .wordmark {
    position: absolute;
    left: 0; right: 0;
    text-align: center;
    font-family: "Montserrat", Arial, sans-serif;
    font-weight: 700;
    color: var(--brand-blue);
    font-size: 52px;
    letter-spacing: 1px;
    line-height: 1;
  }
  .card--front .wordmark { top: 188px; }
  .card--back .wordmark  { top: 265px; }

  .person {
    position: absolute;
    top: 346px; left: 0; right: 0;
    text-align: center;
  }
  .person__name {
    font-family: "Montserrat", Arial, sans-serif;
    font-weight: 600;
    font-size: 21px;
    color: var(--ink-gray);
    line-height: 1.1;
  }
  .person__name .first { color: var(--brand-blue); }
  .person__role {
    font-size: 17px;
    color: var(--text-gray);
    line-height: 1.3;
  }
  .rule {
    position: absolute;
    left: 78px;
    width: 208px;
    height: 1px;
    background: var(--rule);
  }
  .rule--top { top: 397px; }
  .rule--bottom { top: 507px; }

  .contact, .address {
    position: absolute;
    left: 0; right: 0;
    text-align: center;
    font-size: 17px;
    line-height: 21.7px;
    color: var(--text-gray);
  }
  .contact { top: 408px; }
  .contact .label { color: var(--brand-blue); font-weight: 600; }
  .contact .web { color: var(--brand-blue); font-weight: 600; }
  .address { top: 514px; }

  .tagline {
    position: absolute;
    top: 496px; left: 0; right: 0;
    text-align: center;
    font-family: "Montserrat", Arial, sans-serif;
    font-weight: 700;
    font-size: 19px;
    line-height: 24px;
    letter-spacing: -0.3px;
    color: var(--white);
    text-transform: uppercase;
  }
</style>
</head>
<body>
  <section class="card card--front">
    <div class="wordmark">TALVEN</div>
    <div class="person">
      <div class="person__name"><span class="first">MARCUS</span> HALE</div>
      <div class="person__role">Managing Director</div>
    </div>
    <div class="rule rule--top"></div>
    <div class="contact">
      <div><span class="label">P:</span> 020-555 018 274</div>
      <div><span class="label">M:</span> 020-555 018 274</div>
      <div><span class="label">E:</span> hello@talvengroup.com</div>
      <div class="web">www.talvengroup.com</div>
    </div>
    <div class="rule rule--bottom"></div>
    <div class="address">
      <div>48 Harbour Street, Suite 5</div>
      <div>Northbridge, 204518.</div>
    </div>
  </section>

  <section class="card card--back">
    <div class="wordmark">TALVEN</div>
    <div class="tagline">Providing Leadership<br>Delivering Success</div>
  </section>
</body>
</html>
```